Automotive Accessories Business Card

Design a business template that match our new logo design and our industry.

https://www.qelmotorgear.com/

Target Market(s)

Aftermarket auto parts and accessories

Industry/Entity Type

automotive

Contact Information for Business Card

company logo

Font styles to use
Serif
Sans Serif

Colors
EB3D1F
EC4F4E
F09395
F8D3D4
FCEDEE

```html
<!DOCTYPE html>
<html lang="en">
<head>
<meta charset="utf-8">
<title>QEL Motor Gear – Business Card</title>
<link href="https://fonts.googleapis.com/css2?family=Montserrat:wght@400;500;700;800&display=swap" rel="stylesheet">
<style>
  :root {
    --page-bg: #e9e9e9;
    --card-bg: #3b3b3d;
    --card-edge: #d71f26;
    --accent-red: #d71f26;
    --text-light: #f2f2f2;
    --text-muted: #cfcfcf;
    --divider: #8a8a8a;
  }
  * { box-sizing: border-box; margin: 0; padding: 0; }
  html, body {
    width: 1200px; height: 802px; overflow: hidden;
    background: var(--page-bg);
    font-family: "Montserrat", Arial, sans-serif;
  }
  .sheet {
    width: 1200px; height: 802px;
    display: flex; align-items: center; justify-content: center; gap: 50px;
  }
  .card {
    position: relative;
    width: 540px; height: 309px;
    background: var(--card-bg);
    border-bottom: 3px solid var(--card-edge);
    border-right: 3px solid var(--card-edge);
    box-shadow: 0 10px 24px rgba(0,0,0,0.18);
  }
  /* front */
  .brand {
    display: flex; align-items: center; gap: 10px;
    color: var(--text-light);
    font-weight: 800; letter-spacing: 0.5px;
  }
  .brand-square { width: 14px; height: 14px; background: var(--accent-red); }
  .card-front .brand {
    position: absolute; left: 44px; top: 48px; font-size: 26px;
  }
  .identity {
    position: absolute; left: 44px; top: 150px;
    display: flex; align-items: stretch; gap: 20px;
  }
  .person { text-align: right; padding-top: 4px; }
  .person-name {
    color: var(--accent-red); font-weight: 700;
    font-size: 19px; letter-spacing: 2.5px; text-transform: uppercase;
  }
  .person-role { color: var(--text-muted); font-size: 13px; margin-top: 6px; }
  .divider { width: 1px; background: var(--divider); }
  .contacts { list-style: none; color: var(--text-light); font-size: 13px; }
  .contacts li { display: flex; align-items: center; gap: 8px; line-height: 22px; }
  .contacts svg { width: 11px; height: 11px; fill: var(--accent-red); flex: none; }
  .address {
    position: absolute; left: 44px; bottom: 40px;
    color: var(--text-light); font-size: 14px; letter-spacing: 0.3px;
  }
  /* back */
  .card-back { display: flex; align-items: center; justify-content: center; }
  .card-back .brand { font-size: 36px; }
  .card-back .brand-square { width: 20px; height: 20px; }
</style>
</head>
<body>
<main class="sheet">
  <section class="card card-front">
    <div class="brand"><span class="brand-square"></span>QEL MOTOR GEAR INC</div>
    <div class="identity">
      <div class="person">
        <p class="person-name">Marcus Hale</p>
        <p class="person-role">Manager</p>
      </div>
      <span class="divider"></span>
      <ul class="contacts">
        <li><svg viewBox="0 0 24 24"><path d="M6.6 10.8a15.1 15.1 0 0 0 6.6 6.6l2.2-2.2a1 1 0 0 1 1-.25 11.4 11.4 0 0 0 3.6.57 1 1 0 0 1 1 1V20a1 1 0 0 1-1 1A17 17 0 0 1 3 4a1 1 0 0 1 1-1h3.5a1 1 0 0 1 1 1c0 1.25.2 2.45.57 3.6a1 1 0 0 1-.25 1z"/></svg>1-866-555-0142</li>
        <li><svg viewBox="0 0 24 24"><path d="M2 5h20v14H2zm2 2v.5l8 5 8-5V7l-8 5z"/></svg>sales@qelmotorgear.com</li>
        <li><svg viewBox="0 0 24 24"><circle cx="12" cy="12" r="10"/></svg>www.qelmotorgear.com</li>
      </ul>
    </div>
    <p class="address">240 W. Harbor Rd. Unit B, Fairview, CA 91700</p>
  </section>
  <section class="card card-back">
    <div class="brand"><span class="brand-square"></span>QEL MOTOR GEAR INC</div>
  </section>
</main>
</body>
</html>
```